Lantern Crest Pathway

I need a on page electronic flyer for this coaching program. I want a silhouette to accompany the case the copy starts with. I have the copy written but need it put together in a striking way.

Target Market(s)

towards higher net worth individuals

Industry/Entity Type

Electronic

```html
<!DOCTYPE html>
<html lang="en">
<head>
<meta charset="utf-8">
<title>Lantern Crest Pathway – From Financial Worries to Wealth Satisfaction</title>
<link href="https://fonts.googleapis.com/css2?family=Arimo:wght@400;700&display=swap" rel="stylesheet">
<style>
  :root {
    --ink: #111111;
    --paper: #ffffff;
    --title-orange: #f07a12;
    --title-edge: #7a3a00;
    --tagline-blue: #1a2ee0;
    --swoosh-yellow: #fcc200;
    --band-orange: #f26b0f;
    --accent-blue: #3a9fe4;
    --mark-blue: #2f93e8;
    --bar-green: #2cc58a;
    --bar-purple: #9a2fd8;
    --bar-red: #c5261a;
    --bar-olive: #a89a18;
    --photo-dark: #1c2126;
    --photo-light: #9aa6ad;
  }
  html, body {
    margin: 0;
    padding: 0;
    width: 1200px;
    height: 938px;
    overflow: hidden;
    background: var(--paper);
  }
  .canvas {
    position: relative;
    width: 1200px;
    height: 938px;
    overflow: hidden;
  }
  .flyer {
    position: absolute;
    left: 0;
    top: 0;
    width: 930px;
    height: 727px;
    transform: scale(1.2903);
    transform-origin: 0 0;
    font-family: "Arimo", Arial, sans-serif;
    color: var(--ink);
  }
  .shapes {
    position: absolute;
    left: 0;
    top: 0;
    width: 930px;
    height: 727px;
  }
  .headline {
    position: absolute;
    margin: 0;
    font-weight: 700;
    color: var(--title-orange);
    text-shadow: 1px 1px 0 var(--title-edge), -0.5px -0.5px 0 var(--title-edge);
    white-space: nowrap;
  }
  .headline-main { left: 393px; top: 58px; font-size: 20px; }
  .headline-sub { left: 473px; top: 83px; font-size: 18px; }
  .tagline {
    position: absolute;
    left: 413px;
    top: 111px;
    margin: 0;
    font-size: 13.5px;
    color: var(--tagline-blue);
    white-space: nowrap;
  }
  .story {
    position: absolute;
    left: 370px;
    top: 138px;
    width: 492px;
    font-size: 10.8px;
    line-height: 12.6px;
  }
  .story p { margin: 0 0 12.6px; }
  .story p.tight { margin-bottom: 0; }
  .benefits {
    position: absolute;
    left: 447px;
    top: 421px;
    width: 401px;
    margin: 0;
    padding: 0;
    list-style: none;
  }
  .benefits li {
    height: 17px;
    margin-bottom: 1.5px;
    padding-left: 14px;
    font-size: 10.4px;
    line-height: 17px;
    color: var(--paper);
    position: relative;
  }
  .benefits li::before {
    content: "";
    position: absolute;
    left: 5px;
    top: 5px;
    width: 4px;
    height: 4px;
    border-right: 1.6px solid var(--paper);
    border-top: 1.6px solid var(--paper);
    transform: rotate(45deg);
  }
  .benefits .green { background: var(--bar-green); }
  .benefits .purple { background: var(--bar-purple); }
  .benefits .red { background: var(--bar-red); }
  .benefits .olive { background: var(--bar-olive); }
  .contact-line {
    position: absolute;
    left: 470px;
    top: 498px;
    margin: 0;
    font-size: 10.4px;
    font-weight: 700;
    white-space: nowrap;
  }
  .program-mark {
    position: absolute;
    left: 75px;
    top: 424px;
    width: 80px;
    height: 80px;
    border-radius: 50%;
    background: var(--mark-blue);
    display: flex;
    align-items: center;
    justify-content: center;
    text-align: center;
    color: var(--paper);
    font-size: 15px;
    font-weight: 700;
    line-height: 17px;
  }
  .program-summary {
    position: absolute;
    left: 187px;
    top: 491px;
    margin: 0;
    font-size: 12.6px;
    font-weight: 700;
    line-height: 15.6px;
  }
  .facilitator-bio {
    position: absolute;
    right: 62px;
    top: 576px;
    margin: 0;
    font-size: 8.6px;
    font-weight: 700;
    line-height: 10.4px;
    text-align: right;
    white-space: nowrap;
  }
</style>
</head>
<body>
<div class="canvas">
  <div class="flyer">
    <svg class="shapes" viewBox="0 0 930 727">
      <defs>
        <linearGradient id="photoTone" x1="0" y1="0" x2="1" y2="1">
          <stop offset="0" stop-color="#5d6a72"/>
          <stop offset="0.45" stop-color="#9aa6ad"/>
          <stop offset="0.7" stop-color="#3b4349"/>
          <stop offset="1" stop-color="#1c2126"/>
        </linearGradient>
      </defs>
      <rect x="50" y="42" width="827" height="8" fill="#000"/>
      <rect class="case-photo" x="50" y="50" width="302" height="420" fill="url(#photoTone)" role="img" aria-label="Silhouette of a worried man sitting hunched on a chair, head in his hands, before a window overlooking the sea"/>
      <path class="swoosh-orange" d="M50,588 Q330,566 600,596 Q745,562 877,488 L877,625 L50,625 Z" fill="var(--band-orange)"/>
      <path class="swoosh-yellow" d="M50,462 C180,418 360,420 450,468 C500,500 540,560 600,596 Q330,566 50,588 Z" fill="var(--swoosh-yellow)"/>
      <path class="swoosh-rule" d="M560,590 Q740,555 877,483 L877,494 Q744,563 560,590 Z" fill="#000"/>
      <path class="swoosh-accent" d="M150,441 C280,414 392,430 450,468" fill="none" stroke="var(--accent-blue)" stroke-width="3"/>
    </svg>

    <h1 class="headline headline-main">Lantern Crest Pathway</h1>
    <h2 class="headline headline-sub">From Financial Worries to Wealth Satisfaction</h2>
    <p class="tagline">Sometimes the best financial advice isn't about numbers...</p>

    <div class="story">
      <p>A 49 year old attorney, Steve was used to success and rising net worth. But with huge losses in the market crash, layoffs at his firm, his kids heading for college and the stagnant economy stretching ahead, his usual optimism is gone. With his anxiety growing, Steve doubts his own decision making ability. His confidence slipping, he stopped opening his financial statements and could barely speak to his financial advisor. He thought if his advisor said “hang in there” one more time, he just might blow up.</p>
      <p>Yet Steve felt too embarrassed to talk about his deep worries, even with his wife. It seemed like all he could do was pour another glass of wine and suffer in isolation. If you're like Steve, you're afraid and alone with plenty of company. In a September 2009 National Wellbeing Council poll, 80 percent reported the economy is causing significant stress, up from 66 percent from the previous April. The Restful Nights Institute said 27 percent of people surveyed had sleeplessness because of economic anxiety.</p>
      <p class="tight">This process guides you to step back and understand the source of your financial worry—your unique story about the meaning of money. Your money story drives your emotions and decision making—for better and worse. You'll learn a decision making tool for more conscious, effective and satisfying financial and life decisions.</p>
      <p>You'll also examine your core values and strengths—what really matters most to you and how you work at your best. When you use your money and your core strengths to pursue your highest aspirations, life and wealth become balanced. As you commit more fully to your mission and passions, satisfaction grows and money worries melt away.</p>
    </div>

    <ul class="benefits">
      <li class="green">Learn a decision making tool to make choices that truly serve your needs</li>
      <li class="purple">Clarify and more fully engage with your purpose and passions</li>
      <li class="red">Improve your relationship with your financial advisor</li>
      <li class="olive">Feel more in control and confident in your financial life</li>
    </ul>

    <p class="contact-line">For more information, call 267-555-0193. dana.whitfield@example.com</p>

    <div class="program-mark">Anchor<br>Path</div>

    <p class="program-summary">A Six Week Program to :<br>Reduce stress<br>Improve performance<br>Restore Control<br>$995 Money Back Guarantee<br>Dana Whitfield (215)555-0148</p>

    <p class="facilitator-bio">Dana Whitfield, Ph.D. is a psychologist with 30 years<br>of experience treating anxiety and stress. She is<br>co-founder and facilitator of Anchor Path, a peer<br>learning group for high net worth investors.</p>
  </div>
</div>
</body>
</html>
```